Larkfield Ridge Management

I need a professional website. My current website is larkfieldridgemanagement.com and I hate it. It was created with some AI tool very quickly because I needed a site up and running with no advanced notice. I’m open to all designs .. I trust you, the professionals will deliver the results I’m anxiously awaiting! :)

```html
<!DOCTYPE html>
<html lang="en">
<head>
<meta charset="utf-8">
<title>Larkfield Ridge Management — Property Management</title>
<link href="https://fonts.googleapis.com/css2?family=Inter:wght@400;500;600;700;800&display=swap" rel="stylesheet">
<style>
:root{
  --navy:#13294b;
  --navy-deep:#0e2140;
  --red:#c8202a;
  --ink:#1a2233;
  --muted:#4a5365;
  --soft:#f3f5f9;
  --white:#ffffff;
  --line:#3a5075;
}
*{box-sizing:border-box;margin:0;padding:0}
html,body{width:1200px;height:2460px;overflow:hidden}
body{font-family:'Inter',sans-serif;color:var(--ink);background:var(--white);position:relative}
ul{list-style:none}

.site-header{height:101px;display:flex;align-items:center;padding:0 50px 0 56px;background:var(--white);position:relative;z-index:2}
.brand{display:flex;align-items:center;gap:10px;width:200px}
.brand-mark{width:22px;height:22px;background:var(--navy);flex:none}
.brand-name{font-weight:800;font-size:15px;line-height:1.15;color:var(--navy)}
.main-nav{display:flex;gap:38px;margin-left:58px;font-size:13.5px;font-weight:500;color:var(--ink)}
.main-nav a{color:inherit;text-decoration:none;position:relative;padding:6px 0}
.main-nav a.active{color:var(--red)}
.main-nav a.active::after{content:"";position:absolute;left:0;right:0;bottom:-10px;height:3px;background:var(--red)}
.header-phone{margin-left:auto;background:var(--navy);color:var(--white);font-weight:600;font-size:14.5px;height:44px;width:176px;display:flex;align-items:center;justify-content:center;gap:8px;border-radius:3px}

.hero{position:absolute;top:101px;left:0;width:1200px;height:519px;background:linear-gradient(90deg,var(--navy-deep) 0%,#173258 45%,#2b4a72 100%);overflow:hidden}
.hero-photo{position:absolute;right:0;top:0;width:560px;height:519px;background:linear-gradient(180deg,#5e7fa8 0%,#8aa3bf 35%,#6a6f6a 65%,#2b3d3a 85%,#1e3044 100%);opacity:.85;-webkit-mask-image:linear-gradient(90deg,transparent,#000 35%);mask-image:linear-gradient(90deg,transparent,#000 35%)}
.hero-copy{position:absolute;left:95px;top:106px;width:560px;color:var(--white)}
.hero-title{font-size:47px;font-weight:700;line-height:1.14;letter-spacing:-.3px}
.hero-title .accent{color:var(--red)}
.hero-lead{margin-top:26px;font-size:16px;line-height:1.6;color:#e6ebf3}
.hero-actions{display:flex;gap:28px;margin-top:44px}
.btn{height:48px;display:inline-flex;align-items:center;justify-content:center;font-size:14px;font-weight:600;border-radius:2px}
.btn-red{background:var(--red);color:var(--white);width:150px}
.btn-outline{border:1.5px solid var(--white);color:var(--white);width:148px}

.features{position:absolute;top:620px;left:0;width:1200px;height:277px;background:var(--soft);display:flex;padding:0 60px}
.feature{flex:1;text-align:center;padding-top:32px}
.feature svg{width:62px;height:62px}
.feature h3{margin-top:24px;font-size:17px;font-weight:700;color:var(--navy);line-height:1.35}
.feature p{margin-top:12px;font-size:13.5px;line-height:1.6;color:var(--muted)}

.market{position:absolute;top:897px;left:0;width:1200px;height:432px;display:flex}
.market-photo{width:562px;height:432px;background:linear-gradient(180deg,#8fa2b5 0%,#5a6f85 45%,#3e5a3a 80%,#2d3f2a 100%)}
.market-copy{padding:40px 0 0 56px;width:638px}
.rule{width:56px;height:3px;background:var(--red)}
.market-copy h2{margin-top:26px;font-size:25px;font-weight:700;color:var(--navy-deep);line-height:1.35}
.market-copy h2 .accent{color:var(--red)}
.market-copy .intro{margin-top:18px;font-size:13.5px;line-height:1.6;color:var(--ink)}
.checks{margin-top:18px}
.checks li{display:flex;align-items:center;gap:12px;font-size:13.5px;line-height:1;height:29px;color:var(--ink)}
.tick{width:15px;height:15px;flex:none}
.market-copy .outro{margin-top:14px;font-size:13.5px;line-height:1.6}

.why{position:absolute;top:1329px;left:0;width:1200px;height:345px;background:var(--navy)}
.why::before{content:"";position:absolute;left:572px;top:0;width:56px;height:3px;background:var(--red)}
.why h2{text-align:center;color:var(--white);font-size:26px;font-weight:700;padding-top:34px}
.why-cards{display:flex;gap:20px;padding:0 74px;margin-top:26px}
.why-card{flex:1;height:238px;border:1px solid var(--line);border-radius:5px;text-align:center;color:var(--white);padding-top:18px}
.why-card svg{width:60px;height:50px}
.why-card h3{margin-top:14px;font-size:18px;font-weight:700;line-height:1.3}
.why-card p{margin-top:10px;font-size:13.5px;line-height:1.65;color:#dfe6f0}

.who{position:absolute;top:1674px;left:0;width:1200px;height:304px;background:var(--soft);display:flex}
.who-copy{width:619px;padding:40px 0 0 77px}
.who-copy h2{font-size:26px;font-weight:700;color:var(--navy-deep)}
.who-copy .rule{margin-top:12px}
.who-copy .intro{margin-top:22px;font-size:13.5px;line-height:1.6}
.who-copy .checks{margin-top:16px}
.who-photo{width:581px;height:304px;background:linear-gradient(180deg,#9bb0c4 0%,#a3776a 35%,#7d5a4f 60%,#4f7a3f 85%,#3b5e32 100%)}

.cta{position:absolute;top:1978px;left:0;width:1200px;height:167px;background:var(--red);color:var(--white)}
.cta-icon{position:absolute;left:132px;top:28px;width:92px;height:110px}
.cta-copy{position:absolute;left:263px;top:40px}
.cta-copy h2{font-size:22px;font-weight:700;line-height:1.2}
.cta-copy p{margin-top:12px;font-size:13.5px;line-height:1.6;color:#fbe5e6}
.cta-btn{position:absolute;left:746px;top:59px;width:210px;height:54px;background:var(--white);color:var(--ink);font-size:14px;font-weight:600;display:flex;align-items:center;justify-content:center;border-radius:2px}

.site-footer{position:absolute;top:2145px;left:0;width:1200px;height:273px;background:var(--navy);color:var(--white)}
.footer-brand{position:absolute;left:90px;top:38px;width:200px}
.footer-brand .brand-name{color:var(--white);font-size:17px}
.footer-brand .brand-mark{background:var(--white)}
.footer-brand p{margin-top:38px;font-size:13.5px;line-height:1.65;color:#e3e9f2}
.socials{display:flex;gap:24px;margin-top:20px}
.socials span{width:22px;height:22px;border-radius:50%;background:var(--white)}
.footer-col{position:absolute;top:40px}
.footer-col h4{font-size:16px;font-weight:600}
.footer-col ul{margin-top:14px}
.footer-col li{font-size:13.5px;line-height:25px;color:#e3e9f2}
.col-links{left:368px}
.col-services{left:584px}
.col-contact{left:874px}
.col-divider{position:absolute;top:38px;width:1px;height:212px;background:var(--line)}
.contact-list li{display:flex;gap:14px;align-items:flex-start;margin-bottom:6px}
.contact-list svg{width:15px;height:15px;flex:none;margin-top:5px}

.legal{position:absolute;top:2418px;left:0;width:1200px;height:42px;display:flex;align-items:center;padding:0 76px;font-size:11.5px;color:var(--ink)}
.legal nav{margin-left:auto;display:flex;gap:22px}
</style>
</head>
<body>

<header class="site-header">
  <div class="brand"><span class="brand-mark"></span><span class="brand-name">Larkfield Ridge<br>Management</span></div>
  <nav class="main-nav">
    <a class="active">Home</a><a>About Us</a><a>Our Services</a><a>Owners</a><a>Tenants</a><a>Communities</a><a>Contact Us</a>
  </nav>
  <div class="header-phone">
    <svg width="15" height="15" viewBox="0 0 24 24" fill="none" stroke="#fff" stroke-width="2.2"><path d="M5 3h4l2 5-2.5 1.5a11 11 0 0 0 6 6L16 13l5 2v4a2 2 0 0 1-2 2A16 16 0 0 1 3 5a2 2 0 0 1 2-2z"/></svg>
    (440) 555-0187
  </div>
</header>

<section class="hero">
  <div class="hero-photo" role="img" aria-label="City skyline with towers and an arched bridge over a river at golden hour"></div>
  <div class="hero-copy">
    <h1 class="hero-title">Property Management Built for Real-World <span class="accent">Communities.</span></h1>
    <p class="hero-lead">We specialize in managing properties in high Section 8 concentration areas — where others won’t go.<br>It’s not just what we do, it’s what we do best.</p>
    <div class="hero-actions"><span class="btn btn-red">Work With Us</span><span class="btn btn-outline">Our Services</span></div>
  </div>
</section>

<section class="features">
  <div class="feature">
    <svg viewBox="0 0 64 64" fill="none" stroke="#c8202a" stroke-width="2.4" stroke-linejoin="round" stroke-linecap="round"><path d="M6 24l12-10 10 4 8-4 10 2 12 10-6 6"/><path d="M6 24l6 8 14 14a3 3 0 0 0 4-4l-2-2 4 4a3 3 0 0 0 4-4l-2-2 4 3a3 3 0 0 0 4-4l-3-3 3 2a3 3 0 0 0 4-4L40 20l-8 6a4 4 0 0 1-6-4l2-4"/></svg>
    <h3>We Take On<br>What Others Won’t</h3>
    <p>We manage properties in<br>areas most companies<br>consider too challenging.</p>
  </div>
  <div class="feature">
    <svg viewBox="0 0 64 64" fill="none" stroke="#c8202a" stroke-width="2.4" stroke-linejoin="round"><path d="M8 22L32 8l24 14z"/><path d="M10 22h44M12 28h40M16 28v22M24 28v22M32 28v22M40 28v22M48 28v22M10 50h44M6 56h52"/></svg>
    <h3>Strong Housing<br>Authority Connections</h3>
    <p>Direct relationships with NCHA<br>and Maple Trust give us an edge<br>most managers don’t have.</p>
  </div>
  <div class="feature">
    <svg viewBox="0 0 64 64" fill="none" stroke="#c8202a" stroke-width="2.4" stroke-linejoin="round" stroke-linecap="round"><rect x="14" y="10" width="36" height="48" rx="2"/><rect x="24" y="6" width="16" height="8" rx="2"/><path d="M23 34l7 7 12-14"/></svg>
    <h3>End-to-End Leasing<br>&amp; HAP Management</h3>
    <p>We handle the entire process<br>from tenant placement to<br>HAP contract approval.</p>
  </div>
  <div class="feature">
    <svg viewBox="0 0 64 64" fill="none" stroke="#c8202a" stroke-width="2.4" stroke-linejoin="round" stroke-linecap="round"><path d="M32 6l22 8v16c0 14-10 23-22 28C20 53 10 44 10 30V14z"/><path d="M22 31l7 7 13-14"/></svg>
    <h3>Inspections,<br>Done Right</h3>
    <p>We know the standards.<br>We pass inspections.<br>We get tenants in faster.</p>
  </div>
</section>

<section class="market">
  <div class="market-photo" role="img" aria-label="Two-story blue house with a lit front porch at dusk"></div>
  <div class="market-copy">
    <div class="rule"></div>
    <h2>We Know This Market.<br>We Know How to <span class="accent">Win in It.</span></h2>
    <p class="intro">Our focus is simple: help owners get the best possible results<br>from their properties — even in the most difficult zip codes.</p>
    <ul class="checks">
      <li><svg class="tick" viewBox="0 0 16 16"><circle cx="8" cy="8" r="8" fill="#c8202a"/><path d="M4.5 8.2l2.3 2.3 4.7-4.8" fill="none" stroke="#fff" stroke-width="1.8"/></svg>We place quality tenants through proven local connections</li>
      <li><svg class="tick" viewBox="0 0 16 16"><circle cx="8" cy="8" r="8" fill="#c8202a"/><path d="M4.5 8.2l2.3 2.3 4.7-4.8" fill="none" stroke="#fff" stroke-width="1.8"/></svg>We manage the full HAP contract approval process</li>
      <li><svg class="tick" viewBox="0 0 16 16"><circle cx="8" cy="8" r="8" fill="#c8202a"/><path d="M4.5 8.2l2.3 2.3 4.7-4.8" fill="none" stroke="#fff" stroke-width="1.8"/></svg>We work directly with housing authority inspectors</li>
      <li><svg class="tick" viewBox="0 0 16 16"><circle cx="8" cy="8" r="8" fill="#c8202a"/><path d="M4.5 8.2l2.3 2.3 4.7-4.8" fill="none" stroke="#fff" stroke-width="1.8"/></svg>We get properties inspection-ready the first time</li>
      <li><svg class="tick" viewBox="0 0 16 16"><circle cx="8" cy="8" r="8" fill="#c8202a"/><path d="M4.5 8.2l2.3 2.3 4.7-4.8" fill="none" stroke="#fff" stroke-width="1.8"/></svg>We reduce vacancy time and maximize returns</li>
    </ul>
    <p class="outro">Every day without a tenant is lost income. We make sure<br>that doesn’t happen.</p>
  </div>
</section>

<section class="why">
  <h2>Why Owners Choose Larkfield Ridge Management</h2>
  <div class="why-cards">
    <div class="why-card">
      <svg viewBox="0 0 60 50" fill="#fff"><circle cx="30" cy="14" r="7"/><circle cx="15" cy="17" r="5.5"/><circle cx="45" cy="17" r="5.5"/><path d="M18 42c0-9 5-15 12-15s12 6 12 15z"/><path d="M4 42c0-7 4-12 11-12 2 0 3 .3 4 .8-2 3-3 7-3 11.2z"/><path d="M56 42c0-7-4-12-11-12-2 0-3 .3-4 .8 2 3 3 7 3 11.2z"/></svg>
      <h3>Specialized<br>Expertise</h3>
      <p>We focus on Section 8<br>markets — it’s our<br>specialty, not a side<br>service.</p>
    </div>
    <div class="why-card">
      <svg viewBox="0 0 60 50" fill="#fff"><circle cx="30" cy="14" r="7"/><circle cx="15" cy="17" r="5.5"/><circle cx="45" cy="17" r="5.5"/><path d="M18 42c0-9 5-15 12-15s12 6 12 15z"/><path d="M4 42c0-7 4-12 11-12 2 0 3 .3 4 .8-2 3-3 7-3 11.2z"/><path d="M56 42c0-7-4-12-11-12-2 0-3 .3-4 .8 2 3 3 7 3 11.2z"/></svg>
      <h3>Local Relationships<br>That Matter</h3>
      <p>Our connections with NCHA,<br>Maple Trust, and inspectors<br>make a real difference.</p>
    </div>
    <div class="why-card">
      <svg viewBox="0 0 60 50" fill="none" stroke="#fff" stroke-width="3" stroke-linecap="round"><path d="M13 18a19 19 0 1 1-1 12"/><path d="M11 10v9h9"/><path d="M30 14v12l7 5"/></svg>
      <h3>Faster Approvals,<br>Faster Income</h3>
      <p>We get properties approved<br>and tenants in faster —<br>so you start earning sooner.</p>
    </div>
    <div class="why-card">
      <svg viewBox="0 0 60 50" fill="none" stroke="#fff" stroke-width="2.6" stroke-linejoin="round"><rect x="10" y="32" width="7" height="12"/><rect x="24" y="26" width="7" height="18"/><rect x="38" y="20" width="7" height="24"/><path d="M8 24l14-10 10 6 16-12"/><path d="M41 8h7v7"/></svg>
      <h3>Results That<br>Drive Growth</h3>
      <p>We help owners build<br>stronger portfolios in<br>markets others avoid.</p>
    </div>
  </div>
</section>

<section class="who">
  <div class="who-copy">
    <h2>Who We Help</h2>
    <div class="rule"></div>
    <p class="intro">We partner with property owners and investors who have<br>or are looking to build portfolios in:</p>
    <ul class="checks">
      <li><svg class="tick" viewBox="0 0 16 16"><circle cx="8" cy="8" r="8" fill="#c8202a"/><path d="M4.5 8.2l2.3 2.3 4.7-4.8" fill="none" stroke="#fff" stroke-width="1.8"/></svg>High Section 8 concentration neighborhoods</li>
      <li><svg class="tick" viewBox="0 0 16 16"><circle cx="8" cy="8" r="8" fill="#c8202a"/><path d="M4.5 8.2l2.3 2.3 4.7-4.8" fill="none" stroke="#fff" stroke-width="1.8"/></svg>Cleveland and surrounding communities</li>
      <li><svg class="tick" viewBox="0 0 16 16"><circle cx="8" cy="8" r="8" fill="#c8202a"/><path d="M4.5 8.2l2.3 2.3 4.7-4.8" fill="none" stroke="#fff" stroke-width="1.8"/></svg>Areas most management companies won’t touch</li>
    </ul>
  </div>
  <div class="who-photo" role="img" aria-label="Row of brick houses with porches along a tree-lined sidewalk"></div>
</section>

<section class="cta">
  <svg class="cta-icon" viewBox="0 0 92 110" fill="none" stroke="#fff" stroke-width="3" stroke-linejoin="round" stroke-linecap="round"><path d="M6 46L44 10l38 36"/><path d="M14 40v44h26"/><path d="M66 24V12h8v20"/><rect x="24" y="52" width="16" height="16"/><circle cx="62" cy="62" r="14"/><circle cx="62" cy="58" r="4"/><path d="M62 76v28M62 88h8M62 98h6"/></svg>
  <div class="cta-copy">
    <h2>Let’s Build Better Communities —<br>and Better Returns.</h2>
    <p>If others won’t manage it, we will. Let’s talk about how<br>we can help your investment thrive.</p>
  </div>
  <span class="cta-btn">Contact Us Today</span>
</section>

<footer class="site-footer">
  <div class="footer-brand">
    <div class="brand"><span class="brand-mark"></span><span class="brand-name">Larkfield Ridge<br>Management</span></div>
    <p>We manage properties in the communities others won’t — and we do it better.</p>
    <div class="socials"><span aria-label="Social profile"></span><span aria-label="Social profile"></span><span aria-label="Email"></span></div>
  </div>
  <div class="footer-col col-links">
    <h4>Quick Links</h4>
    <ul><li>Home</li><li>About Us</li><li>Our Services</li><li>Owners</li><li>Tenants</li><li>Communities</li><li>Contact Us</li></ul>
  </div>
  <div class="col-divider" style="left:540px"></div>
  <div class="footer-col col-services">
    <h4>Our Services</h4>
    <ul><li>Property Management</li><li>Leasing &amp; Tenant Placement</li><li>HAP Contract Management</li><li>Inspection Coordination</li><li>Maintenance &amp; Repairs</li><li>Financial Reporting</li></ul>
  </div>
  <div class="col-divider" style="left:834px"></div>
  <div class="footer-col col-contact">
    <h4>Contact Info</h4>
    <ul class="contact-list">
      <li><svg viewBox="0 0 24 24" fill="none" stroke="#fff" stroke-width="2"><path d="M5 3h4l2 5-2.5 1.5a11 11 0 0 0 6 6L16 13l5 2v4a2 2 0 0 1-2 2A16 16 0 0 1 3 5a2 2 0 0 1 2-2z"/></svg>(440) 555-0187</li>
      <li><svg viewBox="0 0 24 24" fill="none" stroke="#fff" stroke-width="2"><rect x="3" y="5" width="18" height="14"/><path d="M3 6l9 7 9-7"/></svg>info@larkfieldridgemanagement.com</li>
      <li><svg viewBox="0 0 24 24" fill="none" stroke="#fff" stroke-width="2"><path d="M12 22s7-7 7-12a7 7 0 0 0-14 0c0 5 7 12 7 12z"/><circle cx="12" cy="10" r="2.5"/></svg><span>2750 Harlow Park Dr<br>Suite 310<br>Brookfield Heights, OH 44190</span></li>
    </ul>
  </div>
</footer>

<div class="legal">
  <span>© 2025 Larkfield Ridge Management. All rights reserved.</span>
  <nav><span>Privacy Policy</span><span>|</span><span>Terms of Service</span></nav>
</div>

</body>
</html>
```